Quillmere Capital LLC

Need Professional Business cards for New Investment Fund

Target Market(s)

High Quality investors

Industry/Entity Type

Financial

Contact Information for Business Card

Phone Number +1 555 284 6190
Name Lukas Varenko
Title Fund Manager
email lv@FundQuillmere.com
Website www.FundQuillmere.com

Colors

Designer to choose colors to be used in the design.

Requirements
Must have
• Must have our Logo and all of the above. Must be made so lettering and loge can be raised

```html
<!DOCTYPE html>
<html lang="en">
<head>
<meta charset="utf-8">
<title>Quillmere Capital LLC — Business Card</title>
<link rel="stylesheet" href="https://fonts.googleapis.com/css2?family=Lato:wght@400;700&display=swap">
<style>
  :root {
    --stage: #3a3a3a;
    --card: #111111;
    --card-edge: #1c1c1c;
    --green: #22e01a;
    --olive: #4a5448;
    --text: #d8d8d8;
    --muted: #9a9a9a;
    --divider: #2e2e2e;
    --emboss: #1d1d1d;
  }
  * { box-sizing: border-box; margin: 0; padding: 0; }
  html, body { width: 1200px; height: 1015px; overflow: hidden; }
  body {
    background: var(--stage);
    font-family: "Lato", Arial, sans-serif;
    display: flex;
    flex-direction: column;
    align-items: center;
    justify-content: center;
    gap: 60px;
  }
  .card {
    width: 720px;
    height: 411px;
    background: var(--card);
    border: 1px solid var(--card-edge);
    position: relative;
  }
  /* Back side */
  .card-back {
    display: flex;
    flex-direction: column;
    align-items: center;
    justify-content: center;
  }
  .back-name {
    font-weight: 700;
    font-size: 40px;
    letter-spacing: 3px;
    color: var(--emboss);
    text-transform: uppercase;
    display: flex;
    align-items: center;
    gap: 16px;
    white-space: nowrap;
  }
  .back-name .mark {
    width: 22px; height: 22px;
    background: var(--emboss);
  }
  .back-web {
    margin-top: 70px;
    font-size: 17px;
    letter-spacing: 1.5px;
    color: var(--muted);
  }
  /* Front side */
  .card-front {
    display: flex;
    align-items: center;
  }
  .brand {
    width: 330px;
    display: flex;
    align-items: center;
    justify-content: center;
    gap: 12px;
    font-weight: 700;
    font-size: 30px;
    letter-spacing: 2px;
    color: var(--green);
    text-transform: uppercase;
    white-space: nowrap;
  }
  .brand .mark {
    width: 18px; height: 18px;
    background: var(--green);
  }
  .divider {
    width: 1px;
    height: 150px;
    background: var(--divider);
  }
  .details { padding-left: 40px; }
  .person-name {
    font-weight: 700;
    font-size: 25px;
    letter-spacing: 1px;
    text-transform: uppercase;
  }
  .person-name .first { color: var(--green); }
  .person-name .last { color: var(--olive); }
  .person-title {
    font-size: 17px;
    color: var(--text);
    margin-bottom: 22px;
  }
  .contact-list { list-style: none; }
  .contact-list li {
    display: flex;
    align-items: center;
    gap: 10px;
    font-size: 17px;
    color: var(--text);
    line-height: 1.35;
  }
  .contact-list svg { width: 14px; height: 14px; fill: var(--green); flex: none; }
</style>
</head>
<body>
  <section class="card card-back">
    <div class="back-name"><span class="mark"></span>Quillmere Capital</div>
    <p class="back-web">www.FundQuillmere.com</p>
  </section>

  <section class="card card-front">
    <div class="brand"><span class="mark"></span>Quillmere</div>
    <div class="divider"></div>
    <div class="details">
      <h1 class="person-name"><span class="first">Lukas</span> <span class="last">Varenko</span></h1>
      <p class="person-title">Fund Manager</p>
      <ul class="contact-list">
        <li>
          <svg viewBox="0 0 16 16" aria-hidden="true"><path d="M3 1l3 3-1.5 2a9 9 0 0 0 5.5 5.5L12 10l3 3-2 2C7 15 1 9 1 3z"/></svg>
          +1 555 284 6190
        </li>
        <li>
          <svg viewBox="0 0 16 16" aria-hidden="true"><path d="M1 3h14v10H1z M1 3l7 6 7-6" fill="none" stroke="var(--green)" stroke-width="1.8"/></svg>
          lv@FundQuillmere.com
        </li>
        <li>
          <svg viewBox="0 0 16 16" aria-hidden="true"><circle cx="8" cy="8" r="7"/></svg>
          www.FundQuillmere.com
        </li>
      </ul>
    </div>
  </section>
</body>
</html>
```